Hallowell Kin Playing Cards

We are wanting a cool design for a playing card that includes our logo(s). I will attach our two logos, we are open to using either one of them or another version of them. I will also attach some pictures of card decks to use for inspiration. These are just decks that we have seen from other artists that we liked. We are located in West Texas so although not necessary, a Sotol or Agave or cactus or quail (bird) or some sort of sunset would pay homage to our surroundings. I realize the examples are all very different, but those are just some decks that we like! Thank you!

```html
<!DOCTYPE html>
<html lang="en">
<head>
<meta charset="utf-8">
<title>Hallowell Kin Playing Cards</title>
<link href="https://fonts.googleapis.com/css2?family=Oswald:wght@500;600&display=swap" rel="stylesheet">
<style>
  :root {
    --stage: #050505;
    --card: #f4f4f4;
    --card-edge: #e2e2e2;
    --blue: #5380bd;
    --navy: #2f5a9a;
    --grey: #85888c;
    --dark-card-top: #5a5a5a;
    --dark-card-bottom: #8a8a8a;
    --ink: #1a1a1a;
    --line: #dfe4ea;
    --emblem-fill: #c9d6e8;
  }
  * { box-sizing: border-box; margin: 0; padding: 0; }
  html, body { width: 1200px; height: 1000px; overflow: hidden; background: var(--stage); }
  body { font-family: "Oswald", "Arial Narrow", sans-serif; position: relative; }

  .deck-row { position: absolute; left: 0; width: 1200px; display: flex; justify-content: center; gap: 44px; }
  .deck-row--faces { top: 100px; }
  .deck-row--pack { top: 470px; align-items: flex-end; }

  .card {
    position: relative; width: 200px; height: 290px; border-radius: 10px;
    background: var(--card); box-shadow: inset 0 0 0 1px var(--card-edge);
  }
  .card--dark { background: linear-gradient(160deg, var(--dark-card-top), var(--dark-card-bottom)); box-shadow: none; }
  .card__index { position: absolute; font-weight: 600; font-size: 30px; line-height: 1; }
  .card__index--top { top: 14px; left: 16px; }
  .card__index--bottom { bottom: 14px; right: 16px; transform: rotate(180deg); }
  .card__pip { position: absolute; left: 50%; top: 50%; transform: translate(-50%, -50%); }
  .is-blue { color: var(--blue); fill: var(--blue); }
  .is-grey { color: var(--grey); fill: var(--grey); }
  .is-ink { color: var(--ink); fill: var(--ink); }
  .card--dark .card__index { color: #333; }

  .card-back__rule { position: absolute; left: 24px; right: 24px; height: 10px;
    border-top: 2px solid var(--blue); border-bottom: 2px solid var(--blue); }
  .card-back__rule::after { content: ""; position: absolute; left: 0; right: 0; top: 2px; border-top: 2px solid var(--blue); }
  .card-back__rule--top { top: 40px; }
  .card-back__rule--bottom { bottom: 40px; }
  .card-back__emblem {
    position: absolute; left: 50%; top: 50%; transform: translate(-50%, -50%);
    width: 130px; height: 48px; border-radius: 6px; background: var(--emblem-fill);
  }

  .tuck { display: flex; }
  .tuck-box {
    position: relative; width: 230px; height: 330px; background: var(--card);
    box-shadow: inset 0 0 0 1px var(--card-edge);
  }
  .tuck-box__texture { position: absolute; inset: 12px; border-radius: 4px;
    background: radial-gradient(circle at 50% 40%, #ffffff 0%, var(--line) 100%); }
  .tuck-box__stripes { position: absolute; top: 22px; bottom: 22px; width: 14px;
    border-left: 2px solid var(--blue); border-right: 2px solid var(--blue); }
  .tuck-box__stripes::after { content: ""; position: absolute; top: 0; bottom: 0; left: 4px; border-left: 2px solid var(--blue); }
  .tuck-box__stripes--left { left: 22px; }
  .tuck-box__stripes--right { right: 22px; }
  .tuck-box__brand { position: absolute; top: 96px; left: 44px; right: 44px; text-align: center; }
  .tuck-box__dates { display: flex; justify-content: space-between; padding: 0 6px; font-size: 10px; font-weight: 500; color: var(--blue); letter-spacing: 1px; }
  .tuck-box__name { margin-top: 6px; font-size: 20px; font-weight: 600; color: var(--blue); letter-spacing: 0.5px; line-height: 1.1; }
  .tuck-box__emblem {
    position: absolute; left: 50%; bottom: 42px; transform: translateX(-50%);
    width: 36px; height: 84px; border-radius: 6px; background: var(--emblem-fill);
  }
  .tuck-box__spine {
    width: 56px; height: 330px; background: #e9ecef; position: relative;
    box-shadow: inset 0 0 0 1px var(--card-edge);
  }
  .tuck-box__spine-name { position: absolute; left: 50%; top: 50%; transform: translate(-50%, -50%) rotate(-90deg);
    white-space: nowrap; color: var(--navy); font-weight: 600; font-size: 22px; letter-spacing: 0.5px; }
</style>
</head>
<body>
  <section class="deck-row deck-row--faces" aria-label="Card faces">
    <article class="card" aria-label="Queen of spades">
      <span class="card__index card__index--top is-blue">Q</span>
      <svg class="card__pip is-blue" width="90" height="96" viewBox="0 0 90 96">
        <path d="M45 4 C60 24 88 38 86 58 C84 74 66 80 52 70 L62 92 L28 92 L38 70 C24 80 6 74 4 58 C2 38 30 24 45 4 Z"/>
      </svg>
      <span class="card__index card__index--bottom is-blue">Q</span>
    </article>
    <article class="card" aria-label="Two of hearts">
      <span class="card__index card__index--top is-grey">2</span>
      <svg class="card__pip is-grey" width="92" height="88" viewBox="0 0 92 88">
        <path d="M46 86 L10 48 C-6 30 6 4 26 4 C36 4 42 10 46 18 C50 10 56 4 66 4 C86 4 98 30 82 48 Z"/>
      </svg>
      <span class="card__index card__index--bottom is-grey">2</span>
    </article>
    <article class="card" aria-label="Ace of diamonds">
      <span class="card__index card__index--top is-blue">A</span>
      <svg class="card__pip is-blue" width="70" height="110" viewBox="0 0 70 110">
        <path d="M35 2 L68 55 L35 108 L2 55 Z"/>
      </svg>
      <span class="card__index card__index--bottom is-blue">A</span>
    </article>
    <article class="card card--dark" aria-label="Two of hearts, dark edition">
      <span class="card__index card__index--top">2</span>
      <svg class="card__pip is-ink" width="80" height="78" viewBox="0 0 92 88">
        <path d="M46 86 L10 48 C-6 30 6 4 26 4 C36 4 42 10 46 18 C50 10 56 4 66 4 C86 4 98 30 82 48 Z"/>
      </svg>
      <span class="card__index card__index--bottom">2</span>
    </article>
  </section>

  <section class="deck-row deck-row--pack" aria-label="Card back and tuck box">
    <article class="card card-back" aria-label="Card back">
      <div class="card-back__rule card-back__rule--top"></div>
      <div class="card-back__emblem" role="img" aria-label="Brand emblem area"></div>
      <div class="card-back__rule card-back__rule--bottom"></div>
    </article>

    <div class="tuck">
      <article class="tuck-box" aria-label="Tuck box front">
        <div class="tuck-box__texture" role="img" aria-label="Fine concentric line pattern"></div>
        <div class="tuck-box__stripes tuck-box__stripes--left"></div>
        <div class="tuck-box__stripes tuck-box__stripes--right"></div>
        <div class="tuck-box__brand">
          <div class="tuck-box__dates"><span>SINCE</span><span>1944</span></div>
          <p class="tuck-box__name">HALLOWELL KIN</p>
        </div>
        <div class="tuck-box__emblem" role="img" aria-label="Brand emblem area"></div>
      </article>
      <div class="tuck-box__spine">
        <span class="tuck-box__spine-name">HALLOWELL KIN</span>
      </div>
    </div>
  </section>
</body>
</html>
```